Probate (Legal) Wordpress Design with Coding for Online Company

I need a Wordpress design with coding, pictures, content to be provided by me, fully responsive, and development. This is for a 6-7 page design.

Pages Needed: Home/About/Probate/Process/FAQ/Contact Us/Blog.

The home page should be organized as followed:
-Steps in Probate: Gather; Implement; Close (each step will come with content)
-Flat-Fee Price & Savings: Content will go here with a button to contact us (phone number) or just the phone number.
-You Have Questions, We Have Answers: five questions with content. Only one question answer to show at a time when clicked on the question from the list.
-Get to Know Us: a brief description with content about what we do and who we are.

Main image slogan: Helping Californians deal with loss with DIGNITY & UNDERSTATING (you may use a better slogan if you wish).

The Contact page should not have a map since we are an online company. We service the entire state of California in every county and city.

The About page should be simple, direct, and easy on the eye. It should have a brief description of who we are and it should have no more than 6 reasons why the client should hire us.

About our online California company. We are not attorneys but legal document assistants who prepare legal documents for probate estate when someone dies with or without a will and assets need to be distributed. We have a flat-fee for Formal Probate of $999 and $699 for Informal Probate. We are an online company and offer our services to the entire state of California in every county. We do everything over the phone and email. The turn around time for us to prepare the initial legal paperwork for the client is within 3-5 business days. We can prepare, file, serve and manage a probate matter from petition to closing. We are not attorneys so our prices are very affordable compare to the attorney.

The company name for the website will be www.velmarhollow.com, The Velmar Hollow Group.

I do not have a logo yet. The colors of the website should be easy on the eye and calming. THE SITE SHOULD BE SIMPLE AND STRAIGHT TO THE POINT. EASY TO NAVIGATE.

The company phone number should be very visible and should stand out to the client. It should also be clickable and ready to dial for smartphone users.

I do not want a contact form on the homepage. THE MAIN THING IS FOR THE POTENTIAL CLIENT TO CALL OUR OFFICE TO SIGN UP.

I do like some images of family or people since we are dealing with people who just lost a loved one. Not all the images have to be of people.

The site should not look like we practice law or that people can mistake us for attorneys.

Target Market(s)

People who just lost a loved one who had property, assets, in California but died with or without a will or trust. This is for people looking to hire non-attorneys.

Coding

Coded - Design and coding required

Font styles to use
Serif

Colors

Designer to choose colors to be used in the design.

Requirements
Must have
• Refer to Project Description.
Nice to have
• The sample images provided is what I am attracted to for the homepage image.
Should not have

```html
<!DOCTYPE html>
<html lang="en">
<head>
<meta charset="utf-8">
<title>The Velmar Hollow Group — California Probate Document Assistance</title>
<link rel="stylesheet" href="https://fonts.googleapis.com/css2?family=PT+Serif:wght@400;700&family=Open+Sans:wght@400;600&display=swap">
<style>
:root{
  --olive:#a3ad2b;
  --olive-dark:#8a9322;
  --olive-soft:#e3e6bd;
  --brand-green:#3f7a2c;
  --blue:#1a6fbd;
  --blue-dark:#0f5598;
  --navy:#1e2741;
  --ink:#1f1f1f;
  --text:#6a6a6a;
  --light:#f2f2f2;
  --answer-bg:#eef0dc;
  --white:#ffffff;
  --serif:'PT Serif', Georgia, serif;
  --sans:'Open Sans', Arial, sans-serif;
}
*{box-sizing:border-box;margin:0;padding:0}
html,body{width:1200px;height:3125px;overflow:hidden}
body{position:relative;background:var(--white);font-family:var(--sans);color:var(--text)}
.abs{position:absolute}

/* Header */
.site-header{position:absolute;left:0;top:0;width:1200px;height:108px;background:var(--white)}
.brand{position:absolute;left:104px;top:38px;display:flex;align-items:center;gap:12px}
.brand-mark{width:34px;height:34px;background:var(--olive)}
.brand-name{font-family:var(--serif);font-weight:700;font-size:23px;color:var(--brand-green);letter-spacing:.2px}
.phone-pill{position:absolute;left:787px;top:17px;width:154px;height:30px;background:var(--blue);border-radius:4px;color:var(--white);font-size:12px;font-weight:600;display:flex;align-items:center;padding-left:40px}
.phone-pill .phone-badge{position:absolute;left:-4px;top:-2px;width:34px;height:34px;border-radius:50%;background:var(--white);border:2px solid var(--blue);display:flex;align-items:center;justify-content:center}
.social{position:absolute;left:971px;top:17px;display:flex;gap:5px}
.social span{width:29px;height:29px;border-radius:50%;background:radial-gradient(circle,var(--olive) 0 5px,var(--olive-soft) 6px);border:1px solid #c3c985}
.main-nav{position:absolute;left:0;top:74px;width:1200px;height:24px;font-family:var(--serif);font-weight:700;font-size:15px;color:var(--ink)}
.main-nav a{position:absolute;text-decoration:none;color:inherit}
.main-nav a.current{color:var(--blue)}

/* Hero */
.hero{position:absolute;left:0;top:108px;width:1200px;height:459px;
  background:
    radial-gradient(ellipse 260px 200px at 190px 230px,rgba(40,48,70,.85),rgba(40,48,70,0) 70%),
    radial-gradient(ellipse 200px 180px at 420px 260px,rgba(150,60,70,.55),rgba(150,60,70,0) 70%),
    radial-gradient(ellipse 420px 260px at 870px 110px,rgba(236,238,200,.85),rgba(236,238,200,0) 70%),
    linear-gradient(180deg,rgba(0,0,0,0) 60%,rgba(110,140,40,.9) 100%),
    linear-gradient(90deg,#3e4a2a 0%,#6d7a3e 28%,#a9b37a 55%,#c3c795 72%,#8d9a52 100%)}
.hero-copy{position:absolute;left:527px;top:135px;color:var(--white);font-family:var(--serif);font-weight:700;text-shadow:0 1px 3px rgba(0,0,0,.35)}
.hero-copy .kicker{font-size:27px;line-height:36px}
.hero-copy .headline{font-size:43px;line-height:56px;letter-spacing:.5px}
.btn{position:absolute;display:flex;align-items:center;justify-content:center;background:var(--blue);color:var(--white);font-family:var(--serif);font-weight:700;font-size:15px;text-transform:uppercase;border-bottom:4px solid var(--blue-dark);border-radius:2px}
.slider-dots{position:absolute;left:1075px;top:399px;display:flex;gap:5px}
.slider-dots span{width:14px;height:14px;border-radius:50%;border:2px solid var(--white)}
.slider-dots span.on{background:var(--white)}

/* Steps */
.steps{position:absolute;left:0;top:567px;width:1200px;height:441px;
  background:
    linear-gradient(180deg,rgba(70,73,80,.92) 0%,rgba(80,83,90,.8) 45%,rgba(60,62,68,.9) 100%),
    repeating-linear-gradient(90deg,#5a5d64 0 38px,#484b52 38px 60px,#62656c 60px 84px,#43464d 84px 110px)}
.section-title{position:absolute;left:0;width:1200px;text-align:center;font-family:var(--serif);font-weight:700;font-size:33px;color:var(--ink)}
.steps .section-title{top:68px;color:var(--white)}
.step{position:absolute;top:151px;width:300px;text-align:center;color:var(--white)}
.step .dot{width:88px;height:88px;border-radius:50%;background:var(--olive);margin:0 auto;display:flex;align-items:center;justify-content:center}
.step h3{font-family:var(--serif);font-weight:400;font-size:22px;margin-top:16px}
.step p{font-size:13px;line-height:22px;width:236px;margin:2px auto 0}
.chevrons{position:absolute;top:191px}

/* Who we are */
.who-title{position:absolute;left:104px;top:1094px;font-family:var(--serif);font-weight:700;font-size:33px;color:var(--ink)}
.body-copy{font-size:13px;line-height:24px;color:var(--text)}
.who-text{position:absolute;left:104px;top:1157px;width:430px}
.who-text p+p{margin-top:12px}
.who-photo{position:absolute;left:583px;top:1079px;width:515px;height:325px;border:4px solid #eceef0;box-shadow:0 0 0 1px #d6d8db;
  background:
    radial-gradient(ellipse 110px 170px at 440px 230px,rgba(30,36,58,.95),rgba(30,36,58,0) 75%),
    radial-gradient(ellipse 120px 90px at 90px 250px,rgba(90,120,180,.75),rgba(90,120,180,0) 75%),
    radial-gradient(ellipse 90px 140px at 200px 150px,rgba(245,242,236,.9),rgba(245,242,236,0) 75%),
    radial-gradient(ellipse 110px 90px at 300px 210px,rgba(190,170,160,.7),rgba(190,170,160,0) 75%),
    linear-gradient(180deg,#dfe2e6 0%,#cfd3d9 60%,#b9bec6 100%)}

/* Flat fee */
.flatfee{position:absolute;left:0;top:1481px;width:1200px;height:479px;background:var(--navy)}
.flatfee-photo{position:absolute;left:0;top:0;width:1200px;height:479px;
  background:
    linear-gradient(90deg,rgba(30,39,65,0) 40%,rgba(30,39,65,.75) 55%,var(--navy) 62%),
    radial-gradient(ellipse 220px 120px at 260px 260px,rgba(200,150,140,.8),rgba(200,150,140,0) 75%),
    linear-gradient(175deg,rgba(30,36,60,1) 0%,rgba(40,48,72,.95) 45%,rgba(170,178,196,.9) 72%,#e2e5ec 100%)}
.flatfee h2{position:absolute;left:677px;top:96px;font-family:var(--serif);font-weight:700;font-size:33px;color:var(--white)}
.flatfee .body-copy{position:absolute;left:677px;top:161px;width:430px;color:#e5e7ee}

/* What we do */
.whatwedo .section-title{top:2028px}
.whatwedo-sub{position:absolute;left:330px;top:2086px;width:540px;text-align:center}
.service{position:absolute;top:2170px;width:220px;text-align:center}
.service .icon{height:54px;display:flex;align-items:flex-end;justify-content:center}
.service h3{font-family:var(--serif);font-weight:400;font-size:18px;color:var(--blue);margin-top:14px}

/* FAQ */
.faq{position:absolute;left:0;top:2339px;width:1200px;height:450px;background:var(--light)}
.faq .section-title{top:70px}
.faq-item{position:absolute;left:104px;width:498px;height:38px;background:var(--white);border:1px solid #d4d4d4;font-family:var(--serif);font-size:15px;color:var(--ink);padding-left:34px;display:flex;align-items:center}
.faq-item.active{background:var(--blue);color:var(--white);border-color:var(--blue)}
.faq-answer{position:absolute;left:652px;top:155px;width:448px;height:218px;background:var(--answer-bg);border:2px solid #b9bf83;padding:30px 26px}
.faq-answer p{font-size:13px;line-height:24px;color:#66685a}

/* Footer */
.site-footer{position:absolute;left:0;top:2789px;width:1200px;height:336px;
  background:
    linear-gradient(180deg,rgba(120,128,142,.2) 0%,rgba(120,128,142,0) 40%),
    repeating-linear-gradient(90deg,#8a92a0 0 30px,#7f8797 30px 46px,#939aa8 46px 70px),
    #858d9b}
.footer-col{position:absolute;top:56px;color:var(--white)}
.footer-col h4{font-family:var(--serif);font-weight:700;font-size:18px;margin-bottom:14px}
.footer-col p,.footer-col li{font-size:13px;line-height:20px}
.footer-col ul{list-style:none}
.news li{padding-left:18px;position:relative;margin-bottom:10px}
.news li::before{content:"›";position:absolute;left:2px;top:-1px;font-size:16px}
.footer-social{display:flex;gap:7px;margin-top:22px}
.footer-social span{width:25px;height:25px;border-radius:50%;border:1px solid rgba(255,255,255,.85);background:radial-gradient(circle,rgba(255,255,255,.9) 0 4px,rgba(60,66,80,.55) 5px)}
.footer-rule{position:absolute;left:94px;top:265px;width:1012px;height:1px;background:rgba(255,255,255,.45)}
.copyright{position:absolute;left:0;top:283px;width:1200px;text-align:center;font-size:12px;color:var(--white)}
</style>
</head>
<body>

<header class="site-header">
  <div class="brand"><span class="brand-mark"></span><span class="brand-name">THE VELMAR HOLLOW GROUP</span></div>
  <div class="phone-pill">
    <span class="phone-badge"><svg width="16" height="16" viewBox="0 0 24 24"><path d="M6.6 10.8c1.4 2.8 3.8 5.1 6.6 6.6l2.2-2.2c.3-.3.7-.4 1-.2 1.1.4 2.3.6 3.6.6.6 0 1 .4 1 1V20c0 .6-.4 1-1 1C10.6 21 3 13.4 3 4c0-.6.4-1 1-1h3.5c.6 0 1 .4 1 1 0 1.3.2 2.5.6 3.6.1.3 0 .7-.2 1l-2.3 2.2z" fill="#1a6fbd"/></svg></span>
    +1 555 014 2290
  </div>
  <div class="social"><span></span><span></span><span></span><span></span></div>
  <nav class="main-nav">
    <a class="current" style="left:506px">Home</a>
    <a style="left:592px">About</a>
    <a style="left:677px">Probate</a>
    <a style="left:777px">Process</a>
    <a style="left:875px">FAQ</a>
    <a style="left:948px">Contact Us</a>
    <a style="left:1069px">Blog</a>
  </nav>
</header>

<section class="hero" role="img" aria-label="Young family with two toddlers sitting together on the grass in a sunny park">
  <div class="hero-copy">
    <div class="kicker">Helping Californians deal with loss with</div>
    <div class="headline">DIGNITY &amp; UNDERSTATING</div>
  </div>
  <a class="btn" style="left:529px;top:259px;width:169px;height:46px">Learn More</a>
  <div class="slider-dots"><span class="on"></span><span></span><span></span></div>
</section>

<section class="steps" role="img" aria-label="Muted city skyline at dusk behind the probate steps">
  <h2 class="section-title">Steps In Probate</h2>

  <div class="step" style="left:67px">
    <div class="dot"><svg width="46" height="46" viewBox="0 0 46 46" fill="none" stroke="#fff" stroke-width="3" stroke-linecap="round"><path d="M6 6l12 12M18 10v8h-8M40 6L28 18M28 10v8h8M6 40l12-12M18 36v-8h-8M40 40L28 28M28 36v-8h8"/></svg></div>
    <h3>Gather</h3>
    <p>Lorem ipsum dolor sit amet, conectr adipiscing elit, sed do eiusmod tempor incididunt ut labore magna aliqua.</p>
  </div>
  <svg class="chevrons" style="left:396px" width="34" height="20" viewBox="0 0 34 20" fill="none" stroke="#c8cad0" stroke-width="2.5"><path d="M3 3l7 7-7 7M16 3l7 7-7 7"/></svg>

  <div class="step" style="left:452px">
    <div class="dot"><svg width="44" height="44" viewBox="0 0 44 44" fill="none" stroke="#fff" stroke-width="3" stroke-linejoin="round"><path d="M30 6l8 8-20 20-10 2 2-10z"/><path d="M26 10l8 8"/></svg></div>
    <h3>Implement</h3>
    <p>Lorem ipsum dolor sit amet, conectr adipiscing elit, sed do eiusmod tempor incididunt ut labore magna aliqua.</p>
  </div>
  <svg class="chevrons" style="left:788px" width="34" height="20" viewBox="0 0 34 20" fill="none" stroke="#c8cad0" stroke-width="2.5"><path d="M3 3l7 7-7 7M16 3l7 7-7 7"/></svg>

  <div class="step" style="left:837px">
    <div class="dot"><svg width="44" height="44" viewBox="0 0 44 44" fill="none" stroke="#fff" stroke-width="4" stroke-linecap="round"><path d="M22 5v16"/><path d="M13 11a14 14 0 1 0 18 0"/></svg></div>
    <h3>Close</h3>
    <p>Lorem ipsum dolor sit amet, conectr adipiscing elit, sed do eiusmod tempor incididunt ut labore magna aliqua.</p>
  </div>
</section>

<section class="who">
  <h2 class="who-title">Who We Are ?</h2>
  <div class="who-text body-copy">
    <p>Lorem ipsum dolor sit amet, consectetur adipiscing elit, sed do eiusmod tempor incididunt ut labore et dolore magna aliqua.</p>
    <p>Duis aute irure dolor in reprehenderit in voluptate velit esse cillum dolore eu fugiat nulla pariatur. Excepteur sint occaecat cupidatat non proident, sunt in culpa qui officia deserunt mollit anim id est laborum.</p>
  </div>
  <a class="btn" style="left:104px;top:1329px;width:169px;height:48px">Learn More</a>
  <div class="who-photo" role="img" aria-label="Smiling family of three generations gathered around a table with paperwork"></div>
</section>

<section class="flatfee">
  <div class="flatfee-photo" role="img" aria-label="Close view of a hand signing a document with a fountain pen"></div>
  <h2>Flat-Fee Price &amp; Savings</h2>
  <p class="body-copy">Lorem ipsum dolor sit amet, consectetur adipiscing elit, sed do eiusmod tempor incididunt ut labore et dolore magna aliqua. Ut enim ad minim veniam, quis nostrud exercitation ullamco laboris nisi ut aliquip ex ea commodo consequat. Duis aute irure dolor in reprehenderit in voluptate velit esse cillum dolore eu fugiat nulla pariatur.</p>
  <a class="btn" style="left:677px;top:325px;width:169px;height:48px">Contact Us</a>
</section>

<section class="whatwedo">
  <h2 class="section-title">What We Do ?</h2>
  <p class="whatwedo-sub body-copy">Lorem ipsum dolor sit amet, consectetur adipiscing elit, sed do eiusmod tempor incididunt ut labore et dolore magna aliqua.</p>

  <div class="service" style="left:119px">
    <div class="icon"><svg width="52" height="46" viewBox="0 0 52 46"><rect x="18" y="3" width="16" height="8" rx="2" fill="none" stroke="#a3ad2b" stroke-width="4"/><rect x="2" y="11" width="48" height="32" rx="3" fill="#a3ad2b"/><rect x="2" y="24" width="48" height="3" fill="#fff"/></svg></div>
    <h3>Estate Planning</h3>
  </div>
  <div class="service" style="left:373px">
    <div class="icon"><svg width="56" height="46" viewBox="0 0 56 46" fill="#a3ad2b"><circle cx="28" cy="10" r="7"/><path d="M2 22l8 0 8 12h20l8-12h8l-10 20H12z"/></svg></div>
    <h3>Diligence</h3>
  </div>
  <div class="service" style="left:634px">
    <div class="icon"><svg width="46" height="46" viewBox="0 0 46 46" fill="#a3ad2b"><circle cx="23" cy="12" r="10"/><path d="M3 46c0-13 9-20 20-20s20 7 20 20z"/><path d="M21 26h4l2 12-4 4-4-4z" fill="#fff"/></svg></div>
    <h3>Assistance</h3>
  </div>
  <div class="service" style="left:888px">
    <div class="icon"><svg width="44" height="54" viewBox="0 0 44 54"><rect x="2" y="2" width="40" height="50" rx="3" fill="#a3ad2b"/><rect x="10" y="14" width="24" height="3" fill="#fff"/><rect x="10" y="22" width="24" height="3" fill="#fff"/></svg></div>
    <h3>Guidance</h3>
  </div>
</section>

<section class="faq">
  <h2 class="section-title">Frequently Asked Questions</h2>
  <div class="faq-item active" style="top:159px">Lorem ipsum dolor sit amet consectetur adipiscing elit ?</div>
  <svg class="abs" style="left:601px;top:159px" width="28" height="38" viewBox="0 0 28 38"><path d="M0 0h4l24 19L4 38H0z" fill="#1a6fbd"/></svg>
  <div class="faq-item" style="top:201px">Lorem ipsum dolor sit amet consectetur adipiscing elit ?</div>
  <div class="faq-item" style="top:243px">Lorem ipsum dolor sit amet consectetur adipiscing elit ?</div>
  <div class="faq-item" style="top:285px">Lorem ipsum dolor sit amet consectetur adipiscing elit ?</div>
  <div class="faq-item" style="top:327px">Lorem ipsum dolor sit amet consectetur adipiscing elit ?</div>
  <div class="faq-answer"><p>Lorem ipsum dolor sit amet, consectetur adipiscing elit, sed do eiusmod tempor incididunt ut labore et dolore magna aliqua. Ut enim ad minim veniam, quis nostrud exercitation ullamco laboris nisi ut aliquip ex ea commodo consequat. Duis aute irure dolor in reprehenderit in voluptate velit esse cillum dolore eu fugiat nulla pariatur.</p></div>
</section>

<footer class="site-footer" role="img" aria-label="Faded bay bridge and city skyline behind the footer">
  <div class="footer-col" style="left:127px;width:270px">
    <h4>About Us</h4>
    <p>Lorem ipsum dolor sit amet, consectetur adipiscing elit, sed do eiusmod tempor incidi dunt ut labore et dolore magna aliqua.</p>
    <div class="footer-social"><span></span><span></span><span></span><span></span></div>
  </div>
  <div class="footer-col" style="left:560px">
    <h4>Links</h4>
    <ul><li>Home</li><li>About</li><li>Probate</li><li>Process</li><li>FAQ</li><li>Contact Us</li><li>Blog</li></ul>
  </div>
  <div class="footer-col news" style="left:798px;width:290px">
    <h4>Recent News</h4>
    <ul><li>Sed ut perspiciatis unde omnis iste</li><li>Natus error sit voluptatem accusantium</li><li>Doloremque laudantium, totam rem</li><li>Aperiam, eaque ipsa quae ab illo</li></ul>
  </div>
  <div class="footer-rule"></div>
  <p class="copyright">Copyright © 2017 The Velmar Hollow Group - All Rights Reserved.</p>
</footer>

</body>
</html>
```